Very visible CoWorking Building Sign overlooking downtown LA and 110 freeway

Our building is drab but very visible and in the best location. We need a great sign for our monolith that overlooks downtown LA and the 100 freeway. We are a new CoWorking business and would like to have a few things we do on the sign: private offices, virtual offices, CoWorking Lounge. Everything we have seen is ho-hum. Can you get us noticed? We need people to know what we do and that we are here but in a creative, professional, unique sign.
Target Market(s)
People who have a business in DTLA, remote workers and those who work from home who need a professional address.
Requirements
Must have
- Our logo (which can be somewhat reimagined) which has our address 2417 on it. The three things we focus on: Private Offices, Virtual Offices, CoWorking Lounge. Incorporate some Navy. Readable from several hundred feet away.
Nice to have
- Mural feel? Something inspirational in this crazy COVID times? Graphics? Color block. I like the idea of decorative but it has to be readable as a building sign. The same with the use of colors. Our colors are grays and navy but with a pop of the chartreuse (we have 2 velvet chartreuse chairs in the space). Helpful to view our website: Harborview2417.com.
Should not have
- Not too graffiti. Keep it professional but unique and wow.

```html
<!DOCTYPE html>
<html lang="en">
<head>
<meta charset="utf-8">
<title>Harborview 2417 Building Sign</title>
<link rel="stylesheet" href="https://fonts.googleapis.com/css2?family=Bebas+Neue&display=swap">
<style>
  :root {
    --backdrop: #000000;
    --navy: #1c3560;
    --navy-deep: #15294c;
    --steel: #8a93a6;
    --gray: #c4c4c4;
    --white: #ffffff;
    --ink-line: #2a2a2a;
  }
  html, body {
    margin: 0;
    padding: 0;
    width: 1200px;
    height: 2586px;
    overflow: hidden;
    background: var(--backdrop);
  }
  .sign-canvas {
    display: block;
    width: 1200px;
    height: 2586px;
  }
  .service-line {
    font-family: 'Bebas Neue', 'Arial Narrow', sans-serif;
    fill: var(--white);
    text-anchor: middle;
    letter-spacing: 0.5px;
  }
  .brand-name {
    font-family: 'Bebas Neue', 'Arial Narrow', sans-serif;
    fill: var(--navy);
    text-anchor: middle;
  }
</style>
</head>
<body>
<svg class="sign-canvas" viewBox="0 0 696 1500" xmlns="http://www.w3.org/2000/svg">
  <defs>
    <linearGradient id="workspace-tones" x1="0" y1="0" x2="0" y2="1">
      <stop offset="0" stop-color="#d6c9a8"/>
      <stop offset="0.12" stop-color="#cbbb94"/>
      <stop offset="0.14" stop-color="#e9ead9"/>
      <stop offset="0.22" stop-color="#cfd6c8"/>
      <stop offset="0.30" stop-color="#b99a62"/>
      <stop offset="0.55" stop-color="#8c6a35"/>
      <stop offset="1" stop-color="#5d411c"/>
    </linearGradient>
    <linearGradient id="lounge-tones" x1="0" y1="0" x2="1" y2="1">
      <stop offset="0" stop-color="#6d6a5e"/>
      <stop offset="0.5" stop-color="#8c9a3e"/>
      <stop offset="1" stop-color="#b9a88a"/>
    </linearGradient>
    <clipPath id="banner-clip">
      <rect x="108" y="107" width="482" height="1286"/>
    </clipPath>
  </defs>

  <g class="banner" clip-path="url(#banner-clip)">
    <rect class="workspace-photo" role="img" aria-label="Photo of open coworking floor with white high tables, black bar stools and polished amber concrete floor" x="108" y="107" width="482" height="1286" fill="url(#workspace-tones)"/>

    <rect class="lounge-photo" role="img" aria-label="Photo of lounge area with chartreuse velvet armchairs" x="108" y="1070" width="300" height="323" fill="url(#lounge-tones)"/>

    <polygon class="accent-band-navy" points="108,682 250,846 212,884 108,762" fill="var(--navy)"/>
    <polygon class="accent-band-steel" points="108,782 200,890 180,912 108,830" fill="var(--steel)" opacity="0.6"/>

    <polygon class="corner-gray" points="470,872 590,782 590,1050 515,1135" fill="var(--gray)"/>
    <line class="corner-rule" x1="413" y1="822" x2="515" y2="918" stroke="var(--ink-line)" stroke-width="2"/>
    <line class="corner-rule" x1="430" y1="812" x2="530" y2="905" stroke="var(--ink-line)" stroke-width="1.5"/>

    <polygon class="corner-white" points="312,1393 590,1393 590,1048 428,1235" fill="var(--white)"/>

    <polygon class="service-diamond" points="344,748 580,1014 344,1280 108,1014" fill="var(--navy)" stroke="var(--white)" stroke-width="4" stroke-linejoin="miter"/>

    <g class="service-list">
      <text class="service-line" x="330" y="937" font-size="50">PRIVATE &amp;</text>
      <text class="service-line" x="330" y="1003" font-size="50">VIRTUAL OFFICES</text>
      <text class="service-line" x="326" y="1088" font-size="50">COWORKING</text>
      <text class="service-line" x="326" y="1155" font-size="50">LOUNGE</text>
    </g>

    <g class="brand-mark">
      <text class="brand-name" x="500" y="1290" font-size="26">HARBORVIEW</text>
      <text class="brand-name" x="500" y="1362" font-size="80">2417</text>
    </g>
  </g>
</svg>
</body>
</html>
```